Web Design Project

We are looking to for a redesign for www.volketa.com. Volketa Systems is a Managed Service Provider of IT solutions based is Calgary, Alberta, Canada. We are currently expanding into the Edmonton market and would like to lauch our new site with our expansion.
The design should be sleak in style and communicate a professional vision to our clients and prospects.

Thanks,
Dale

Target Market(s)

Small to medium size businesses looking to outsource or complement their IT solutions.

Industry/Entity Type

It Professional

```html
<!DOCTYPE html>
<html lang="en">
<head>
<meta charset="utf-8">
<title>Volketa – Managed IT Service Professionals</title>
<link rel="stylesheet" href="https://fonts.googleapis.com/css2?family=Play:wght@400;700&family=Roboto:wght@300;400&display=swap">
<style>
:root{
  --ink:#1e1e1e;
  --bar:#202020;
  --header:#dadada;
  --page:#f3f3f3;
  --panel:#d9d9d9;
  --hero-light:#f4f4f4;
  --hero-dark:#c9c9c9;
  --accent:#e3202a;
  --muted:#bdbdbd;
  --footer:#3a3a3a;
  --footer-text:#d4d4d4;
}
*{box-sizing:border-box;margin:0;padding:0}
html,body{width:1200px;height:1140px;overflow:hidden}
body{background:var(--page);font-family:"Roboto",Arial,sans-serif;color:var(--ink);position:relative}
.top-rule{position:absolute;left:0;top:0;width:1200px;height:7px;background:#111}
.site-header{position:absolute;left:0;top:7px;width:1200px;height:95px;background:var(--header)}
.brand{position:absolute;left:157px;top:26px;display:flex;align-items:center;gap:12px}
.brand-mark{width:14px;height:14px;border-radius:50%;background:var(--accent)}
.brand-name{font-family:"Play",sans-serif;font-size:34px;letter-spacing:1px;color:var(--ink);font-weight:400;line-height:40px}
.utility-links{position:absolute;right:157px;top:19px;font-size:12px;color:var(--ink)}
.utility-links span{margin:0 7px}
.social{position:absolute;right:159px;top:47px;display:flex;gap:9px}
.social span{width:34px;height:34px;background:var(--bar);border-radius:3px;display:block}
.main-nav{position:absolute;left:157px;top:121px;width:886px;height:53px;background:var(--bar);border-radius:6px 6px 0 0;display:flex;align-items:center;font-family:"Play",sans-serif;font-size:16px}
.main-nav a{color:#eee;text-decoration:none;padding:0 25px;border-right:1px solid #3c3c3c;line-height:36px}
.main-nav a:last-of-type{border-right:none}
.main-nav a.active{color:var(--accent);padding-left:20px}
.search{position:absolute;right:19px;top:13px;display:flex;height:29px}
.search .field{width:145px;background:#2c2c2c;border:1px solid #444}
.search .button{width:73px;background:#111;color:#999;font-size:13px;display:flex;align-items:center;justify-content:center;font-family:"Roboto",sans-serif}
.hero{position:absolute;left:157px;top:174px;width:886px;height:343px;background:radial-gradient(ellipse at 75% 20%,var(--hero-light),#dcdcdc 55%,var(--hero-dark));overflow:hidden}
.hero h1{position:absolute;left:41px;top:62px;font-family:"Play",sans-serif;font-weight:400;font-size:32px;line-height:39px;color:#111}
.hero p{position:absolute;left:41px;top:149px;width:440px;font-size:12px;line-height:16.6px;font-weight:300;color:#222}
.btn{position:absolute;background:linear-gradient(#4a4a4a,#111);color:#eee;border-radius:6px;font-family:"Play",sans-serif;display:flex;align-items:center;justify-content:center;box-shadow:0 1px 2px rgba(0,0,0,.5)}
.hero .btn{left:42px;top:234px;width:163px;height:37px;font-size:15px}
.hero-photo{position:absolute;right:0;top:0;width:340px;height:343px;background:linear-gradient(90deg,rgba(160,160,160,0),#9a9a9a 40%,#8a8a8a)}
.dots{position:absolute;left:413px;top:305px;display:flex;gap:11px}
.dots span{width:13px;height:13px;border-radius:50%;background:#fff;border:1px solid #999}
.feature{position:absolute;top:540px;width:277px;height:302px;background:var(--panel)}
.feature h2{height:43px;background:var(--bar);color:#eee;font-family:"Play",sans-serif;font-weight:400;font-size:21px;text-align:center;line-height:43px}
.feature .photo{position:absolute;left:23px;top:65px;width:231px;height:99px}
.feature p{position:absolute;left:20px;top:178px;width:237px;font-size:12.5px;line-height:16.6px;text-align:justify;text-align-last:justify;font-weight:300}
.feature .btn{left:85px;top:248px;width:108px;height:33px;font-size:13.5px}
.feature::after{content:"";position:absolute;left:30px;right:30px;bottom:-14px;height:14px;background:radial-gradient(ellipse at top,rgba(0,0,0,.22),transparent 70%)}
.partner-photo{background:linear-gradient(#1a1a1a,#6a6a6a 50%,#1a1a1a);display:flex;align-items:center;justify-content:center;color:#fff;font-family:"Play",sans-serif;font-size:15px}
.clients-title{position:absolute;left:0;width:1200px;top:862px;text-align:center;font-family:"Play",sans-serif;font-size:21px;font-weight:400;color:#111}
.carousel{position:absolute;left:157px;top:902px;width:886px;height:107px;background:var(--panel);display:flex}
.arrow{width:33px;height:107px;background:var(--muted);display:flex;align-items:center;justify-content:center}
.client{display:flex;align-items:center;justify-content:center;border-right:1px solid #c4c4c4;font-family:"Play",sans-serif;font-size:17px;color:#333;gap:7px}
.client:last-of-type{border-right:none}
.client i{width:12px;height:12px;border-radius:50%;background:#555;display:block}
.site-footer{position:absolute;left:0;top:1062px;width:1200px;height:78px;background:var(--footer);color:var(--footer-text);font-size:12px}
.footer-links{position:absolute;left:157px;top:21px}
.footer-links span{margin:0 18px}
.copyright{position:absolute;left:157px;top:42px}
.credit{position:absolute;right:157px;top:21px}
</style>
</head>
<body>
<div class="top-rule"></div>
<header class="site-header">
  <div class="brand"><span class="brand-mark"></span><span class="brand-name">VOLKETA</span></div>
  <div class="utility-links">Home<span>|</span>Quick Contact<span>|</span>Sitemap</div>
  <div class="social" aria-label="Social links"><span></span><span></span><span></span></div>
</header>

<nav class="main-nav">
  <a class="active">Home</a><a>About Us</a><a>Solutions</a><a>Services</a><a>Contact Us</a>
  <div class="search"><div class="field"></div><div class="button">Search</div></div>
</nav>

<section class="hero">
  <h1>Managed IT Service<br>Professionals..!</h1>
  <p>Volketa Systems employs an innovative managed service solution to provide our clients with technical expertise and superb customer service. Our goal is to ensure that our clients business requirements align with their technical needs in order to maximize their benefits</p>
  <div class="btn">Read More</div>
  <div class="hero-photo" role="img" aria-label="Photo of a smiling businessman in a light suit pointing upward"></div>
  <div class="dots"><span></span><span></span><span></span></div>
</section>

<article class="feature" style="left:157px">
  <h2>Edmonton market</h2>
  <div class="photo" role="img" aria-label="Photo of glass office towers seen from below" style="background:linear-gradient(135deg,#8a7a5a,#c9d6e6 45%,#4c5a6e)"></div>
  <p>Lorem Ipsum is simply dummy text of the printing and typesetting industry. Lorem Ipsum has been the industry's standard</p>
  <div class="btn">Read More</div>
</article>
<article class="feature" style="left:462px">
  <h2>Partners</h2>
  <div class="photo partner-photo">Orvane</div>
  <p>Lorem Ipsum is simply dummy text of the printing and typesetting industry. Lorem Ipsum has been the industry's standard</p>
  <div class="btn">Read More</div>
</article>
<article class="feature" style="left:766px">
  <h2>Live Support</h2>
  <div class="photo" role="img" aria-label="Photo of a support agent wearing a headset with colleagues behind" style="background:linear-gradient(90deg,#cfd8d0,#e7ece6 50%,#c49a7e)"></div>
  <p>Lorem Ipsum is simply dummy text of the printing and typesetting industry. Lorem Ipsum has been the industry's standard</p>
  <div class="btn">Read More</div>
</article>

<h2 class="clients-title">Clients</h2>
<section class="carousel">
  <div class="arrow"><svg width="16" height="28" viewBox="0 0 16 28"><path d="M16 0V28L0 14Z" fill="#fff"/></svg></div>
  <div class="client" style="width:181px">Tallora</div>
  <div class="client" style="width:150px">Redfern Co</div>
  <div class="client" style="width:161px"><i></i>Ivo Marchet</div>
  <div class="client" style="width:159px">Pellum</div>
  <div class="client" style="width:169px">Brightnest</div>
  <div class="arrow"><svg width="16" height="28" viewBox="0 0 16 28"><path d="M0 0V28L16 14Z" fill="#fff"/></svg></div>
</section>

<footer class="site-footer">
  <div class="footer-links">Home<span>|</span>About Us<span>|</span>Solutions<span>|</span>Services<span>|</span>Contact Us</div>
  <div class="copyright">2012 ©- Volketa. All Rights Reserved</div>
  <div class="credit">Powerd by : Stackhaven</div>
</footer>
</body>
</html>
```